Meadowrun Acres Website Design

We have been redeveloping our website already and are quite happy with the content, but the design needs to be better:
https://tilvexa-hub.examplehost.net/

Pages, content, concept etc. Can all be taken from the redeveloped website.
The farmer can register and edit/view their profile, subscribe and these pages need to be designed better as well as contact, about, pricing, tos, privacy and a page with example portlets.

We need a website to appeal to farmers, investors and retiring farmers.

The design should be clean and a little country.

We don't want any repeat designs that some may submit to every project and has no respect for the project brief, so please don't submit them.

Target Market(s)

farmers, investors, retirees

Industry/Entity Type

Farming

Number of Pages Required

5+ page

Colors

Designer to choose colors to be used in the design.

Requirements
Must have
• Nice, clean modern design that is appealing
• Profile page laid out nicely

```html
<!DOCTYPE html>
<html lang="en">
<head>
<meta charset="utf-8">
<title>Meadowrun Acres</title>
<link href="https://fonts.googleapis.com/css2?family=Roboto:wght@300;400;500;700&family=Lora:ital@1&display=swap" rel="stylesheet">
<style>
:root{
  --green:#3aa142;
  --green-dark:#235c2c;
  --green-band:#43a84b;
  --ink:#333;
  --muted:#666;
  --light:#f3f4f6;
  --white:#fff;
}
*{box-sizing:border-box;margin:0;padding:0}
html,body{width:1200px;height:3203px;overflow:hidden}
body{font-family:'Roboto',Arial,sans-serif;color:var(--ink);background:var(--white);position:relative}
.section-title{font-weight:300;font-size:27px;text-align:center;text-transform:uppercase;letter-spacing:.5px;color:#444}
.title-rule{width:96px;height:3px;background:var(--green);margin:14px auto 0}

/* header */
.site-header{height:98px;display:flex;align-items:center;padding:0 85px;background:var(--white);box-shadow:0 1px 4px rgba(0,0,0,.08);position:relative;z-index:2}
.brand{display:flex;align-items:center;gap:12px;font-size:26px;font-weight:500;color:var(--green-dark)}
.brand-dot{width:36px;height:36px;border-radius:50%;border:3px solid var(--green)}
.main-nav{margin-left:auto;display:flex;align-items:center;gap:26px;font-size:12.5px;text-transform:uppercase;color:#555}
.main-nav .active{color:var(--green)}
.search-btn{width:48px;height:48px;border:2px solid #555;border-radius:50%;display:flex;align-items:center;justify-content:center}

/* hero */
.hero{height:519px;position:relative;background:linear-gradient(180deg,#9aa7a4 0%,#6f7a5e 40%,#7c8a4e 70%,#8b8d5a 100%)}
.hero-copy{position:absolute;right:85px;top:130px;width:360px;text-align:right;color:var(--white)}
.hero-copy h1{font-weight:400;font-size:36px;margin-bottom:18px}
.hero-copy p{font-size:12.5px;line-height:1.9}
.btn{display:inline-block;background:var(--green);color:var(--white);font-size:14px;text-transform:uppercase;padding:12px 18px;border-radius:2px;margin-top:16px}
.hero-dots{position:absolute;left:50%;bottom:18px;transform:translateX(-50%);display:flex;gap:24px}
.hero-dots span{width:12px;height:12px;border:2px solid var(--white);border-radius:50%}

/* welcome */
.welcome{height:489px;padding-top:40px}
.welcome-intro{text-align:center;font-size:12px;line-height:2.1;color:var(--muted);margin:26px auto 0;width:800px}
.audiences{display:flex;justify-content:center;gap:56px;margin-top:40px}
.audience{width:292px;text-align:center}
.audience-icon{width:120px;height:120px;border-radius:50%;background:var(--green);border:5px solid var(--white);box-shadow:0 0 0 3px var(--green);margin:0 auto;display:flex;align-items:center;justify-content:center}
.audience-icon.dark{background:var(--green-dark);box-shadow:0 0 0 3px var(--green-dark)}
.audience h3{font-size:17px;font-weight:500;color:var(--green);margin:22px 0 12px}
.audience h3.dark{color:var(--green-dark)}
.audience p{font-size:12px;line-height:2.2;color:var(--muted)}

/* own a farm */
.own-farm{height:376px;background:var(--light);display:flex;gap:48px;padding:52px 0 0 120px}
.video{width:426px;height:265px;background:linear-gradient(135deg,#4b3a34,#7a2a33 45%,#3f5e86);position:relative}
.play{position:absolute;left:50%;top:50%;width:52px;height:52px;margin:-26px 0 0 -26px;border-radius:50%;background:#e42b2b;border:3px solid var(--white)}
.play:after{content:"";position:absolute;left:19px;top:14px;border-left:16px solid var(--white);border-top:10px solid transparent;border-bottom:10px solid transparent}
.own-copy h2{font-weight:300;font-size:25px;text-transform:uppercase;color:#444;margin:4px 0 26px}
.own-copy p{font-size:11.5px;line-height:2.1;color:var(--muted);width:480px}
.ticks{list-style:none;margin-top:18px}
.ticks li{font-size:11.5px;color:var(--muted);line-height:2.2;display:flex;align-items:center;gap:14px}

/* testimonials */
.testimonials{height:410px;background:var(--green-band);color:var(--white);text-align:center;padding-top:62px;position:relative}
.testimonials .section-title{color:var(--white)}
.testimonials .title-rule{background:var(--white)}
.quote-mark{width:68px;height:68px;border:2px solid var(--white);border-radius:50%;margin:26px auto 28px;display:flex;align-items:center;justify-content:center;background:rgba(255,255,255,.1)}
.testimonials blockquote{font-size:12px;line-height:2.3;width:720px;margin:0 auto}
.stars{margin:18px 0 8px;font-size:14px;letter-spacing:3px}
.author{font-size:12.5px;font-weight:500;text-transform:uppercase}
.place{font-size:12px;margin-top:6px}
.arrow{position:absolute;top:160px}

/* blog */
.blog{height:493px;padding-top:42px}
.posts{display:flex;gap:20px;justify-content:center;margin-top:30px}
.post{width:330px}
.post-photo{height:139px}
.post h3{font-size:13px;font-weight:700;text-transform:uppercase;margin:26px 0 10px}
.post p{font-size:11.5px;line-height:1.9;color:var(--muted)}
.post-meta{font-family:'Lora',serif;font-style:italic;font-size:12px;color:var(--green);margin-top:14px;display:flex;gap:18px;align-items:center}
.post-meta span{display:flex;align-items:center;gap:6px}

/* how it works */
.how{height:483px;background:var(--light);padding-top:40px}
.steps{display:flex;justify-content:center;gap:52px;margin-top:38px}
.step{width:285px;height:320px;background:var(--white);border:1px solid #e3e3e3;text-align:center;padding:36px 24px 0}
.step-icon{width:86px;height:78px;margin:0 auto}
.step h3{font-size:14px;font-weight:500;color:var(--green);line-height:1.6;margin:22px 0 10px}
.step p{font-size:11.5px;line-height:2.1;color:var(--muted)}
.step-link{display:inline-block;font-size:12px;font-weight:500;color:var(--green);text-transform:uppercase;border-bottom:1px solid var(--green);margin-top:14px}

/* footer */
.site-footer{height:335px;background:var(--green-dark);color:var(--white);position:relative}
.footer-cols{display:flex;padding:50px 0 0 118px}
.footer-brand{width:260px;text-align:center;padding-top:28px}
.footer-brand .brand-dot{width:90px;height:90px;border-color:#7ac27f;margin:0 auto 22px}
.footer-brand span{font-size:26px}
.footer-col{width:248px}
.footer-col h4{font-size:16px;font-weight:500;text-transform:uppercase;margin-bottom:26px}
.contact-list{list-style:none;font-size:11px}
.contact-list li{display:flex;gap:12px;margin-bottom:16px;line-height:1.5}
.footer-col p{font-size:11px;line-height:1.9}
.email-field{width:210px;height:34px;background:var(--white);color:#888;font-size:11px;padding:10px 14px;margin-top:18px}
.sub-btn{display:inline-block;background:var(--green);font-size:10px;text-transform:uppercase;padding:6px 9px;margin-top:12px}
.socials{display:flex;gap:7px;margin-top:20px}
.socials span{width:36px;height:36px;border:2px solid var(--white);border-radius:50%;display:flex;align-items:center;justify-content:center}
.copyright{position:absolute;left:0;right:0;bottom:30px;text-align:center;font-size:11px}
</style>
</head>
<body>

<header class="site-header">
  <div class="brand"><span class="brand-dot"></span>Meadowrun Acres</div>
  <nav class="main-nav">
    <span class="active">Home</span><span>Aspiring Farmers</span><span>Investors</span><span>Retiring Farmer</span><span>Blog</span><span>Pricing</span><span>Contact</span>
    <span class="search-btn"><svg width="14" height="14" viewBox="0 0 14 14"><circle cx="6" cy="6" r="4.5" fill="none" stroke="#333" stroke-width="2"/><line x1="9.5" y1="9.5" x2="13" y2="13" stroke="#333" stroke-width="2"/></svg></span>
  </nav>
</header>

<section class="hero" role="img" aria-label="Family walking with a rider on horseback and cattle grazing in a green paddock beneath wooded hills">
  <div class="hero-copy">
    <h1>Meadowrun Acres</h1>
    <p>We know how hard it is for a young family to find the capital required to own and operate their own farm.</p>
    <span class="btn">Read More</span>
  </div>
  <div class="hero-dots"><span></span><span></span></div>
</section>

<section class="welcome">
  <h2 class="section-title">Welcome to Meadowrun Acres</h2>
  <div class="title-rule"></div>
  <p class="welcome-intro">We know how hard it is for a young family to find the capital required to own and operate their own farm - so we started Meadowrun Acres.<br>rejuvenate regional Australia by putting farming back up the top of the career list for anyone.</p>
  <div class="audiences">
    <div class="audience">
      <div class="audience-icon">
        <svg width="60" height="50" viewBox="0 0 60 50" aria-hidden="true"><path d="M6 18h10l26-14v42L16 32H6z" fill="#fff"/><rect x="14" y="32" width="8" height="14" rx="2" fill="#fff"/><path d="M48 16q6 9 0 18M52 10q10 15 0 30" fill="none" stroke="#fff" stroke-width="3" stroke-linecap="round"/></svg>
      </div>
      <h3>Appeal</h3>
      <p>We have these best aspiring farmers at our fingertips because we know what they want out of farming. We sionate &amp; the best fit for your operation.</p>
    </div>
    <div class="audience">
      <div class="audience-icon dark">
        <svg width="56" height="60" viewBox="0 0 56 60" aria-hidden="true"><path d="M20 10h16l-5 8h-6z" fill="#fff"/><path d="M25 18h6c14 6 20 18 20 28 0 8-6 12-23 12S5 54 5 46c0-10 6-22 20-28z" fill="#fff"/><text x="28" y="49" text-anchor="middle" font-family="Roboto,Arial,sans-serif" font-size="22" font-weight="700" fill="#235c2c">$</text></svg>
      </div>
      <h3 class="dark">Investors</h3>
      <p>We have these best aspiring farmers at our fingertips because we know what they want out of farming. We sionate &amp; the best fit for your operation.</p>
    </div>
    <div class="audience">
      <div class="audience-icon">
        <svg width="56" height="56" viewBox="0 0 56 56" aria-hidden="true"><path d="M8 28L28 10l20 18" fill="none" stroke="#fff" stroke-width="4" stroke-linejoin="round" stroke-linecap="round"/><path d="M14 26v22h28V26" fill="#fff"/><rect x="24" y="34" width="8" height="14" fill="#3aa142"/></svg>
      </div>
      <h3>Retiring Farmers</h3>
      <p>We have these best aspiring farmers at our fingertips because we know what they want out of farming. We sionate &amp; the best fit for your operation.</p>
    </div>
  </div>
</section>

<section class="own-farm">
  <div class="video" role="img" aria-label="Video still of a young farmer standing in front of a blue tractor"><span class="play"></span></div>
  <div class="own-copy">
    <h2>You Can Own a Farm</h2>
    <p>I really love to farm as farming is forever. I would love to farm anywhere there is an opportunity to live and work in a local farming community.We know how hard it is for a young family to find the capital required to own and operate their own farm</p>
    <ul class="ticks">
      <li><svg width="10" height="9" viewBox="0 0 10 9"><path d="M1 5l3 3 5-7" fill="none" stroke="#3aa142" stroke-width="2"/></svg>We connect a young farming family</li>
      <li><svg width="10" height="9" viewBox="0 0 10 9"><path d="M1 5l3 3 5-7" fill="none" stroke="#3aa142" stroke-width="2"/></svg>With a retiring farming family</li>
      <li><svg width="10" height="9" viewBox="0 0 10 9"><path d="M1 5l3 3 5-7" fill="none" stroke="#3aa142" stroke-width="2"/></svg>Investors</li>
      <li><svg width="10" height="9" viewBox="0 0 10 9"><path d="M1 5l3 3 5-7" fill="none" stroke="#3aa142" stroke-width="2"/></svg>Own and operate a farm together</li>
    </ul>
  </div>
</section>

<section class="testimonials">
  <svg class="arrow" style="left:140px" width="18" height="130" viewBox="0 0 18 130"><path d="M16 2L2 65l14 63" fill="none" stroke="rgba(255,255,255,.6)" stroke-width="2"/></svg>
  <svg class="arrow" style="right:140px" width="18" height="130" viewBox="0 0 18 130"><path d="M2 2l14 63-14 63" fill="none" stroke="rgba(255,255,255,.6)" stroke-width="2"/></svg>
  <h2 class="section-title">Our Testimonials</h2>
  <div class="title-rule"></div>
  <div class="quote-mark"><svg width="26" height="20" viewBox="0 0 26 20" aria-hidden="true"><path d="M0 20V11C0 5 3 1 9 0l1 3c-3 1-5 3-5 6h5v11zM15 20V11c0-6 3-10 9-11l1 3c-3 1-5 3-5 6h5v11z" fill="#fff"/></svg></div>
  <blockquote>Meadowrun Acres can offer an opportunity to put people with the skills and ambition, with either a farming family looking to transition into retirement or for someone who doesn't have the skills but has capital and wants somewhere safe to invest. Meadowrun Acres or who doesn't have the skills but has capital and wants somewhere safe to invest.</blockquote>
  <div class="stars">☆☆☆☆☆</div>
  <div class="author">Callum Dorsey, Aspiring Farmer</div>
  <div class="place">Tallowbrook Queensland</div>
</section>

<section class="blog">
  <h2 class="section-title">Latest Blog</h2>
  <div class="title-rule"></div>
  <div class="posts">
    <article class="post">
      <div class="post-photo" role="img" aria-label="Family with two small children sitting on a farm verandah" style="background:linear-gradient(135deg,#7b5a48,#a8724f 50%,#6c6a5e)"></div>
      <h3>Out of the Griddle House</h3>
      <p>Tom Ashby, of Griddle House origins, unpacks why regenerative farming is the future</p>
      <div class="post-meta"><span><svg width="11" height="11" viewBox="0 0 11 11"><rect x=".5" y="1.5" width="10" height="9" fill="none" stroke="#3aa142"/><line x1="0" y1="4" x2="11" y2="4" stroke="#3aa142"/></svg>9 days ago</span><span><svg width="11" height="11" viewBox="0 0 11 11"><path d="M1 1h9v6H4l-3 3z" fill="none" stroke="#3aa142"/></svg>05 Comments</span></div>
    </article>
    <article class="post">
      <div class="post-photo" role="img" aria-label="Market garden rows under a blue sky with hills behind" style="background:linear-gradient(180deg,#4d8fd6 0%,#a9c8ea 45%,#5e7a3c 70%,#3f6b2a)"></div>
      <h3>Rowan is a cool name, so is Tess</h3>
      <p>Rowan and Tess both hold a huge passion to own and operate their own farm.</p>
      <div class="post-meta"><span><svg width="11" height="11" viewBox="0 0 11 11"><rect x=".5" y="1.5" width="10" height="9" fill="none" stroke="#3aa142"/><line x1="0" y1="4" x2="11" y2="4" stroke="#3aa142"/></svg>few seconds ago</span><span><svg width="11" height="11" viewBox="0 0 11 11"><path d="M1 1h9v6H4l-3 3z" fill="none" stroke="#3aa142"/></svg>05 Comments</span></div>
    </article>
    <article class="post">
      <div class="post-photo" role="img" aria-label="Interior of a timber shearing shed" style="background:linear-gradient(135deg,#4a3527,#8a6a4c 55%,#5b4434)"></div>
      <h3>Weekly Update 12 April 2017</h3>
      <p>Meadowrun Acres TV Tom provides another update on progress with Meadowrun Acres</p>
      <div class="post-meta"><span><svg width="11" height="11" viewBox="0 0 11 11"><rect x=".5" y="1.5" width="10" height="9" fill="none" stroke="#3aa142"/><line x1="0" y1="4" x2="11" y2="4" stroke="#3aa142"/></svg>few seconds ago</span><span><svg width="11" height="11" viewBox="0 0 11 11"><path d="M1 1h9v6H4l-3 3z" fill="none" stroke="#3aa142"/></svg>05 Comments</span></div>
    </article>
  </div>
</section>

<section class="how">
  <h2 class="section-title">How It Works</h2>
  <div class="title-rule"></div>
  <div class="steps">
    <div class="step">
      <svg class="step-icon" viewBox="0 0 86 78" role="img" aria-label="Registration form icon"><rect x="22" y="8" width="42" height="62" rx="3" fill="none" stroke="#3aa142" stroke-width="3"/><rect x="34" y="3" width="18" height="10" rx="2" fill="#3aa142"/><path d="M30 30l4 4 7-8M30 46l4 4 7-8" fill="none" stroke="#3aa142" stroke-width="3"/><path d="M46 31h10M46 47h10M30 62h26" stroke="#3aa142" stroke-width="3"/></svg>
      <h3>Register as an Aspiring<br>Farmer</h3>
      <p>I really love to farm as farming is forever. I would love to farm anywhere there is an own and operate their own farm</p>
      <span class="step-link">Register</span>
    </div>
    <div class="step">
      <svg class="step-icon" viewBox="0 0 86 78" role="img" aria-label="Sprouting seedling icon"><path d="M43 72V34" stroke="#3aa142" stroke-width="4"/><path d="M43 40C43 22 30 14 14 16c0 16 12 26 29 24z" fill="#3aa142"/><path d="M43 34c0-16 12-26 30-24 0 16-12 26-30 24z" fill="#3aa142"/><path d="M18 72h50" stroke="#3aa142" stroke-width="4" stroke-linecap="round"/></svg>
      <h3>Build your farm skills to<br>get yourself</h3>
      <p>I really love to farm as farming is forever. I would love to farm anywhere there is an own and operate their own farm</p>
      <span class="step-link">Farm-Ready</span>
    </div>
    <div class="step">
      <svg class="step-icon" viewBox="0 0 86 78" role="img" aria-label="Farm house and sun icon"><circle cx="66" cy="16" r="8" fill="#3aa142"/><path d="M10 40L38 16l28 24" fill="none" stroke="#3aa142" stroke-width="4" stroke-linejoin="round"/><path d="M18 36v34h40V36" fill="#3aa142"/><rect x="32" y="50" width="12" height="20" fill="#fff"/><path d="M4 72h78" stroke="#3aa142" stroke-width="4" stroke-linecap="round"/></svg>
      <h3>Together we find you your<br>dream farm</h3>
      <p>I really love to farm as farming is forever. I would love to farm anywhere there is an own and operate their own farm</p>
      <span class="step-link">Match Making</span>
    </div>
  </div>
</section>

<footer class="site-footer">
  <div class="footer-cols">
    <div class="footer-brand"><div class="brand-dot"></div><span>Meadowrun Acres</span></div>
    <div class="footer-col">
      <h4>Contact Us</h4>
      <ul class="contact-list">
        <li><svg width="12" height="12" viewBox="0 0 12 12"><path d="M2 1h3l1 3-2 1a7 7 0 003 3l1-2 3 1v3a1 1 0 01-1 1A10 10 0 011 2a1 1 0 011-1z" fill="#fff"/></svg>(000)-555-0142 &nbsp;(Phone)</li>
        <li><svg width="12" height="12" viewBox="0 0 12 12"><rect x="1" y="4" width="10" height="6" fill="#fff"/><rect x="3" y="1" width="6" height="3" fill="#fff"/></svg>(000)-555-0143 &nbsp;(Fax)</li>
        <li><svg width="12" height="12" viewBox="0 0 12 12"><rect x="1" y="2" width="10" height="8" fill="#fff"/><path d="M1 2l5 4 5-4" fill="none" stroke="#235c2c"/></svg><u>hello@meadowrunacres.net</u></li>
        <li><svg width="12" height="14" viewBox="0 0 12 14"><path d="M6 0a5 5 0 00-5 5c0 4 5 9 5 9s5-5 5-9a5 5 0 00-5-5z" fill="#fff"/><circle cx="6" cy="5" r="2" fill="#235c2c"/></svg>Unit #2, 18 Sample Road, Harrow<br>Vale Street North</li>
      </ul>
    </div>
    <div class="footer-col">
      <h4>Newsletter</h4>
      <p>Register Your email address to get information about us</p>
      <div class="email-field">Email Address</div>
      <span class="sub-btn">Subscribe</span>
    </div>
    <div class="footer-col">
      <h4>Follow Us</h4>
      <p>Stay in touch with our farming families and hear the latest news from the paddock each week.</p>
      <div class="socials">
        <span><svg width="14" height="14" viewBox="0 0 14 14"><rect x="1" y="3" width="12" height="8" fill="none" stroke="#fff" stroke-width="1.5"/><path d="M1 3l6 5 6-5" fill="none" stroke="#fff" stroke-width="1.5"/></svg></span>
        <span><svg width="14" height="14" viewBox="0 0 14 14"><circle cx="7" cy="7" r="6" fill="none" stroke="#fff" stroke-width="1.5"/><path d="M1 7h12M7 1c-3 3-3 9 0 12M7 1c3 3 3 9 0 12" fill="none" stroke="#fff" stroke-width="1.2"/></svg></span>
        <span><svg width="14" height="14" viewBox="0 0 14 14"><circle cx="3" cy="7" r="2" fill="#fff"/><circle cx="11" cy="3" r="2" fill="#fff"/><circle cx="11" cy="11" r="2" fill="#fff"/><path d="M3 7l8-4M3 7l8 4" stroke="#fff" stroke-width="1.3"/></svg></span>
        <span><svg width="14" height="14" viewBox="0 0 14 14"><path d="M7 12S1 8 1 4.5A3 3 0 017 3a3 3 0 016 1.5C13 8 7 12 7 12z" fill="#fff"/></svg></span>
        <span><svg width="14" height="14" viewBox="0 0 14 14"><path d="M2 1h3l1 3-2 1a7 7 0 004 4l1-2 3 1v3a1 1 0 01-1 1A11 11 0 011 2a1 1 0 011-1z" fill="#fff"/></svg></span>
      </div>
    </div>
  </div>
  <div class="copyright">© 2017 Copyright Meadowrun Acres.All rights reserved</div>
</footer>

</body>
</html>
```